Jolly Paws Business Card Update

I have a business card which I love. I want to keep the same logo, colours, font and style. I want to upgrade the scripting and remove some elements and add others.
On the front side under Services - remove the existing wording and insert - Providing individual coaching strategies to create happy, healthy and social canine companions
Under Denise Carvell amend the current wording to read: Qualified in Dog Behavioural Training, Natural Animal Healthcare and Animal Health Science
On the reverse side to remove the web address.

```html
<!DOCTYPE html>
<html lang="en">
<head>
<meta charset="utf-8">
<title>Jolly Paws Business Card</title>
<link href="https://fonts.googleapis.com/css2?family=Oxygen:wght@400;700&family=Arimo:wght@400;700&display=swap" rel="stylesheet">
<style>
  :root {
    --page-bg: #d9d4cf;
    --card-light: #f3f4f5;
    --card-mid: #e4e7ea;
    --blue: #1b78c4;
    --blue-deep: #0f5ea6;
    --red: #c2232c;
    --red-deep: #8f1d22;
    --navy: #2a3482;
    --cream: #f1ead7;
    --band-text: #f6dcdc;
    --band-title: #eeeeee;
  }
  * { margin: 0; padding: 0; box-sizing: border-box; }
  html, body { width: 1200px; height: 1054px; overflow: hidden; }
  body { background: var(--page-bg); position: relative; font-family: "Oxygen", sans-serif; }

  .card {
    position: absolute; left: 80px; top: 214px;
    width: 1040px; height: 626px;
    border-radius: 26px; overflow: hidden;
    box-shadow: 0 14px 40px rgba(0,0,0,0.22);
  }
  .card-art { position: absolute; inset: 0; }

  .brand-name {
    position: absolute; left: 62px; top: 294px; width: 324px;
    text-align: center; font-family: "Oxygen", sans-serif; font-weight: 700;
    font-size: 40px; color: var(--navy);
  }

  .identity { position: absolute; right: 46px; top: 58px; text-align: right; color: var(--navy); }
  .identity .name { font-size: 38px; font-weight: 700; line-height: 50px; }
  .identity .qualifications { font-size: 22px; line-height: 33px; margin-top: 4px; }

  .contacts { position: absolute; right: 46px; top: 226px; list-style: none; color: var(--navy); }
  .contacts li { display: flex; justify-content: flex-end; align-items: center; font-size: 24px; line-height: 37px; }
  .contacts svg { width: 24px; height: 24px; margin-left: 16px; flex: none; }

  .services { position: absolute; right: 46px; top: 374px; text-align: right; font-family: "Arimo", sans-serif; }
  .services h2 { font-size: 25px; font-weight: 700; color: var(--band-title); line-height: 34px; }
  .services p { font-size: 24px; color: var(--band-text); line-height: 31.5px; }

  .mission {
    position: absolute; right: 46px; top: 530px; text-align: right;
    font-family: "Arimo", sans-serif; font-size: 24px; line-height: 32px; color: var(--navy);
  }
</style>
</head>
<body>
  <div class="card">
    <svg class="card-art" width="1040" height="626" viewBox="0 0 1040 626" aria-hidden="true">
      <defs>
        <linearGradient id="frost" x1="0" y1="0" x2="1" y2="1">
          <stop offset="0" stop-color="#f7f8f9"/>
          <stop offset="1" stop-color="#e2e5e8"/>
        </linearGradient>
        <linearGradient id="blueFill" x1="0" y1="0" x2="1" y2="0">
          <stop offset="0" stop-color="#1f7fcb"/>
          <stop offset="1" stop-color="#146aae"/>
        </linearGradient>
        <linearGradient id="bandFill" x1="0" y1="0" x2="1" y2="0">
          <stop offset="0" stop-color="#c2232c"/>
          <stop offset="1" stop-color="#8f1d22"/>
        </linearGradient>
      </defs>
      <rect class="card-base" width="1040" height="626" fill="url(#frost)"/>
      <rect class="services-band" x="300" y="362" width="740" height="158" fill="url(#bandFill)"/>
      <rect class="mission-strip" x="300" y="520" width="740" height="80" fill="#f1eeee" opacity="0.8"/>
      <path class="edge-arc" d="M390 0 Q520 250 410 626" fill="none" stroke="#c2232c" stroke-width="16"/>
      <path class="blue-panel" d="M0 0 H390 Q510 250 400 626 H0 Z" fill="url(#blueFill)"/>
      <circle class="brand-disc" cx="224" cy="316" r="162" fill="#f1ead7"/>
    </svg>

    <div class="brand-name">Jolly Paws</div>

    <div class="identity">
      <h1 class="name">Denise Carvell</h1>
      <p class="qualifications">Qualified in Dog Behavioural<br>Training, Natural Animal Healthcare<br>and Animal Health Science</p>
    </div>

    <ul class="contacts">
      <li>0412 587 206
        <svg viewBox="0 0 24 24"><rect x="6" y="2" width="12" height="20" rx="2" fill="none" stroke="#c2232c" stroke-width="2"/><rect x="9" y="5" width="6" height="6" fill="#c2232c"/><circle cx="12" cy="17" r="1.5" fill="#c2232c"/></svg>
      </li>
      <li>jollypaws1@mailbox.com
        <svg viewBox="0 0 24 24"><rect x="2" y="6" width="20" height="13" fill="#c2232c"/><path d="M2 6 L12 13 L22 6" fill="none" stroke="#f3f4f5" stroke-width="1.6"/></svg>
      </li>
      <li>www.jollypaws1.com
        <svg viewBox="0 0 24 24"><circle cx="12" cy="12" r="8" fill="none" stroke="#c2232c" stroke-width="2"/><path d="M4 12 H20 M12 4 V20 M12 4 Q6 12 12 20 M12 4 Q18 12 12 20" fill="none" stroke="#c2232c" stroke-width="1.5"/></svg>
      </li>
    </ul>

    <div class="services">
      <h2>SERVICES</h2>
      <p>Providing individual coaching<br>strategies to create happy, healthy<br>and social canine companions</p>
    </div>

    <p class="mission">Promoting communication and connection<br>between dogs &amp; their families</p>
  </div>
</body>
</html>
```